Yoga class opening. Little schedule for JUNE JULY and AUGUST

Flyer to promote an opening yoga class. The color of the docx haven't to be respected.

We want something joyfull, professional, clean and serious.

About the logo we oppened a contest at the same time so at the moment there is no logo but the logo color will be simple.

The phone number will change so you can poste a random one for the design that i can change by myself.

i recieved many creation in both side BUT i want something in 1 side :)

Target Market(s)

Yoga student. all age

Industry/Entity Type

It Professional

Logo Text

Yoga fern

Font styles to use
Sans Serif

Requirements
Must have
• The text present on the docx
Nice to have
• Some symbols about yoga ( Namasté signs, mandala, ... )
Should not have
• Not too much details it has to be clear.

```html
<!DOCTYPE html>
<html lang="fr">
<head>
<meta charset="utf-8">
<title>Yoga fern – Ouverture du studio</title>
<link rel="stylesheet" href="https://fonts.googleapis.com/css2?family=Montserrat:wght@500;700&family=Oswald:wght@500;600;700&family=Roboto+Condensed:ital,wght@0,400;0,700;1,400&display=swap">
<style>
  :root{
    --orange:#e8772a;
    --orange-deep:#c8501e;
    --orange-dark:#8e3412;
    --blue:#2a7cc0;
    --navy:#1d4f8c;
    --sky-light:#9fd3f0;
    --sky-deep:#2a86c8;
    --panel:#d9e9f6;
    --panel-line:#b7d2ea;
    --paper:#ffffff;
    --backdrop:#ececec;
  }
  *{box-sizing:border-box;margin:0;padding:0}
  html,body{width:1200px;height:831px;overflow:hidden;background:var(--backdrop)}
  .flyer{position:absolute;left:310px;top:6px;width:580px;height:819px;background:var(--paper);overflow:hidden;font-family:"Roboto Condensed",sans-serif;color:var(--navy)}

  .brand-mark{position:absolute;left:20px;top:16px;width:78px;height:78px;border-radius:50%;background:var(--orange-deep)}
  .brand-name{position:absolute;left:112px;top:10px;font-family:"Montserrat",sans-serif;font-weight:500;font-size:62px;letter-spacing:1px;color:var(--orange);line-height:1}

  .tagline{position:absolute;right:20px;top:82px;text-align:right;font-family:"Oswald",sans-serif;line-height:1.05}
  .tagline .lead{font-size:19px;font-weight:600;color:var(--navy)}
  .tagline .opening{font-size:25px;font-weight:600;color:var(--orange-deep);margin-top:2px}
  .tagline .address{font-size:16px;font-weight:500;color:var(--orange);margin-top:3px}

  .ribbon{position:absolute;left:-6px;top:124px;width:196px;height:40px;background:var(--orange-deep);color:#fff;font-family:"Oswald",sans-serif;font-weight:700;font-size:27px;line-height:40px;padding-left:24px;letter-spacing:1px}
  .ribbon-fold{position:absolute;left:0;top:164px}

  .hero-photo{position:absolute;left:0;top:182px;width:580px;height:148px;background:linear-gradient(180deg,var(--sky-light) 0%,#5eaee0 55%,var(--sky-deep) 100%)}

  .ornament{position:absolute;left:362px;top:240px;width:186px;height:186px;border-radius:50%;background:radial-gradient(circle,#ffffff 0%,#ffffff 38%,#f6c9a6 62%,#e8894a 100%)}

  .intro{position:absolute;left:0;top:330px;width:330px;height:46px;background:var(--orange);color:#fff;font-style:italic;font-size:11.5px;line-height:1.25;padding:7px 12px 0 14px}

  .schedule{position:absolute;left:0;top:376px;width:330px;bottom:0;background:var(--panel);padding:8px 14px 0 14px}
  .month{margin-bottom:9px}
  .month-title{font-family:"Oswald",sans-serif;font-weight:600;font-size:19px;color:var(--navy);line-height:1.1;border-bottom:1px solid var(--panel-line)}
  .session-title{font-size:9px;font-weight:700;color:var(--blue);margin:3px 0 2px}
  .session-row{display:flex;justify-content:space-between;font-size:9.5px;line-height:12px;color:var(--navy);padding-left:6px}

  .accent-edge{position:absolute;right:0;top:330px;width:5px;height:395px;background:var(--orange)}

  .info{position:absolute;left:338px;top:440px;width:236px;text-align:center;color:var(--blue)}
  .info .start{font-size:17px;line-height:1.15}
  .info .date{font-family:"Oswald",sans-serif;font-weight:700;font-size:23px;color:var(--navy);margin-top:2px}
  .info .more{font-size:13px;margin-top:12px}
  .info .phone{font-family:"Oswald",sans-serif;font-weight:700;font-size:32px;color:var(--blue);line-height:1.1}
  .info .page{font-size:18px;margin-top:4px}
  .info .online{font-size:16px;font-weight:700;color:var(--navy);margin-top:2px}

  .closing{position:absolute;left:346px;top:720px;width:234px;height:86px}
  .closing-text{position:absolute;inset:0;display:flex;flex-direction:column;justify-content:center;align-items:center;font-family:"Oswald",sans-serif;font-weight:700;font-size:27px;line-height:1.05;color:#fff}
</style>
</head>
<body>
<main class="flyer">
  <header>
    <div class="brand-mark"></div>
    <div class="brand-name">YOGA FERN</div>
    <div class="tagline">
      <p class="lead">NOUVEAU !! VOTRE STUDIO DE YOGA A IXELLES</p>
      <p class="opening">OUVERTURE LE 6 JUIN 2016 AU</p>
      <p class="address">12 RUE DES TILLEULS</p>
      <p class="address">1050 IXELLES</p>
    </div>
    <div class="ribbon">NOUVEAU !!</div>
    <svg class="ribbon-fold" width="10" height="8" viewBox="0 0 10 8"><polygon points="0,0 10,0 10,8" fill="var(--orange-dark)"/></svg>
  </header>

  <div class="hero-photo" role="img" aria-label="Photo d'une personne en méditation devant des montagnes bleues"></div>

  <p class="intro">En attendant le planning des cours de la rentrée, YOGA FERN vous propose ses stages et ateliers d'été.</p>

  <section class="schedule">
    <div class="month">
      <h2 class="month-title">JUIN</h2>
      <p class="session-title">STAGE DÉCOUVERTE DU YOGA 65 €</p>
      <p class="session-row"><span>Du 6 au 10 juin</span><span>10h00 · 18h00</span></p>
      <p class="session-row"><span>Du 13 au 17 juin</span><span>10h00 · 18h00</span></p>
      <p class="session-row"><span>Du 20 au 24 juin</span><span>10h00 · 18h00</span></p>
      <p class="session-title">ATELIER GESTION DU STRESS 35 €</p>
      <p class="session-row"><span>Samedi 11 juin</span><span>10h00 · 12h00</span></p>
      <p class="session-row"><span>Samedi 25 juin</span><span>10h00 · 12h00</span></p>
    </div>
    <div class="month">
      <h2 class="month-title">JUILLET</h2>
      <p class="session-title">STAGE INITIATION À L'ASHTANGA 70 €</p>
      <p class="session-row"><span>Du 4 au 8 juillet</span><span>10h00 · 18h00</span></p>
      <p class="session-row"><span>Du 11 au 15 juillet</span><span>10h00 · 18h00</span></p>
      <p class="session-row"><span>Du 18 au 22 juillet</span><span>10h00 · 18h00</span></p>
      <p class="session-title">ATELIER RESPIRATION ET RELAXATION 35 €</p>
      <p class="session-row"><span>Samedi 9 juillet</span><span>10h00 · 12h00</span></p>
      <p class="session-row"><span>Samedi 23 juillet</span><span>10h00 · 12h00</span></p>
    </div>
    <div class="month">
      <h2 class="month-title">AOUT</h2>
      <p class="session-title">STAGE DÉCOUVERTE DU YOGA 65 €</p>
      <p class="session-row"><span>Du 1 au 5 août</span><span>10h00 · 18h00</span></p>
      <p class="session-row"><span>Du 8 au 12 août</span><span>10h00 · 18h00</span></p>
      <p class="session-row"><span>Du 22 au 26 août</span><span>10h00 · 18h00</span></p>
    </div>
  </section>

  <div class="ornament" role="img" aria-label="Mandala décoratif orange et bleu avec le symbole Om au centre"></div>
  <div class="accent-edge"></div>

  <section class="info">
    <p class="start">Démarrage<br>du planning annuel le</p>
    <p class="date">5 septembre 2016</p>
    <p class="more">Plus d'info et inscription :</p>
    <p class="phone">612 345 678</p>
    <p class="page">Ou via notre page</p>
    <p class="online">en ligne : yoga fern</p>
  </section>

  <div class="closing">
    <svg width="234" height="86" viewBox="0 0 234 86"><polygon points="14,4 234,0 234,80 0,86" fill="var(--orange-deep)"/></svg>
    <div class="closing-text"><span>UN BEL ETE</span><span>A TOUS !</span></div>
  </div>
</main>
</body>
</html>
```